Coastal Learner Bureau business cards

Australian company about to start offering its services. We recruit international students to come to study English, vocational education and postgraduate courses in Australia. We help them find the institution and select the right city they want to come to Australia. We are a young, online oriented and supportive agency. Our clients are between 18 and 35 years old, mainly University students, young professionals or people with work experience. We provide much more information that any other agency offer. We administrate a Facebook group with more than 11.000 members that daily ask questions about general information when coming to Australia, while they are here and even after they leave the country

Target Market(s)

International students from South America, Central America and Europe

Industry/Entity Type

Student

Contact Information for Business Card

Tomas Bilbrea
Managing Director
tomas@kelvarin.com.au
www.kelvoria.com.au
+61 491058264
Melbourne, Australia

Font styles to use
Serif
Sans Serif

Colors

Designer to choose colors to be used in the design.

Requirements
Must have
• Horizontal design
• Standard business card size and shape. If font uses green or yellow colours, they will have to match the ones from the logo
Nice to have
• UPDATE: Use the contents of the green image to design one of the card sides. Use our logo in the background of that side as watermark.
• Passport image, or immigration stamps. A picture of the Yarra River (from Melbourne) would be cool as well.
Should not have
• Non-standard business card size and shape
• Not black as the background colour of any sides as we are not a VIP agency or a hight class service. We are orientes to young people and they like colours, pictures, something attractive.
• Vertical design
• NO YELLOW or BLACK AS THE BACKGROUND COLOUR OF ANY SIDE OF THE BIZ CARD

```html
<!DOCTYPE html>
<html lang="en">
<head>
<meta charset="utf-8">
<title>Coastal Learner Bureau – Business Cards</title>
<link rel="stylesheet" href="https://fonts.googleapis.com/css2?family=Open+Sans:wght@400;700&family=Kalam:wght@700&display=swap">
<style>
  :root {
    --brand-green: #0b5a2e;
    --brand-gold: #e6b92a;
    --ink: #1c1c1c;
    --card: #ffffff;
    --backdrop: #e4e4e4;
  }
  * { margin: 0; padding: 0; box-sizing: border-box; }
  html, body {
    width: 1200px;
    height: 900px;
    overflow: hidden;
    background: var(--backdrop);
    font-family: "Open Sans", Arial, sans-serif;
  }
  .canvas {
    position: relative;
    width: 1200px;
    height: 900px;
  }
  .card {
    position: absolute;
    left: 300px;
    width: 600px;
    height: 366px;
    background: var(--card);
    box-shadow: 0 6px 18px rgba(0,0,0,0.18);
  }
  .card--front { top: 48px; }
  .card--back  { top: 476px; }

  .brand-name {
    font-family: "Open Sans", Arial, sans-serif;
    font-weight: 700;
    color: var(--brand-green);
    line-height: 1.05;
  }
  .card--front .brand-lockup {
    position: absolute;
    inset: 0;
    display: flex;
    align-items: center;
    justify-content: center;
    gap: 14px;
  }
  .card--front .brand-name { font-size: 30px; }
  .brand-dot {
    width: 18px;
    height: 18px;
    border-radius: 50%;
    background: var(--brand-gold);
    flex: none;
  }

  .card--back .brand-lockup {
    position: absolute;
    left: 36px;
    top: 110px;
    width: 250px;
    display: flex;
    align-items: flex-start;
    gap: 12px;
  }
  .card--back .brand-name { font-size: 40px; }
  .card--back .brand-dot { width: 24px; height: 24px; margin-top: 10px; }

  .contact {
    position: absolute;
    left: 330px;
    top: 84px;
    font-size: 15px;
    color: var(--ink);
    line-height: 1.3;
  }
  .contact__name { color: var(--brand-green); font-weight: 700; }
  .contact__group { margin-bottom: 10px; }
  .contact__company { color: var(--brand-green); }

  .tagline {
    position: absolute;
    right: 30px;
    bottom: 28px;
    font-family: "Kalam", "Comic Sans MS", cursive;
    font-weight: 700;
    font-size: 27px;
    color: var(--brand-green);
  }
</style>
</head>
<body>
<main class="canvas">
  <section class="card card--front" aria-label="Business card front">
    <div class="brand-lockup">
      <span class="brand-dot"></span>
      <span class="brand-name">Coastal Learner Bureau</span>
    </div>
  </section>

  <section class="card card--back" aria-label="Business card back">
    <div class="brand-lockup">
      <span class="brand-dot"></span>
      <span class="brand-name">Coastal Learner Bureau</span>
    </div>

    <address class="contact" style="font-style: normal;">
      <div class="contact__group">
        <div class="contact__name">Tomas Bilbrea</div>
        <div>Managing Director</div>
      </div>
      <div class="contact__group">
        <div class="contact__company">Coastal Learner Bureau</div>
        <div>Melbourne, Australia</div>
      </div>
      <div class="contact__group">
        <div>+61 491058264</div>
        <div>tomas@kelvarin.com.au</div>
        <div>www.kelvoria.com.au</div>
      </div>
    </address>

    <p class="tagline">Hacemos más por ti!</p>
  </section>
</main>
</body>
</html>
```